Mara Penrith Copywriter Website

I am starting a new business as a freelance copywriter. Trying to set up the website for my business is proving to be too technical for me. I would like a simple, clean website using primarily black and white. I have attached the logo I would like used. I would like the menu icons to be Home, Services, Portfolio, Blog, Contact. I would like my mobile phone number (0412 583 906) and email address (mara.penrith.copywriter@fernmail.test) used in the header of the site. I need the site to be easily manageable and inter-changeable for me to be able to move things around and add images, etc with ease.

I would like the home page to be a static page with space for an image of myself somewhere (I haven't had this taken as yet), an area to put a bit about myself and my business, and also somewhere to include social media icons/links. Again, I would like the whole website and home page to be easily managed so that I can add/delete things with ease.

I would like the image of the typewriter used in the website somewhere also please.

Coding

Coded - Design and coding required

Number of Pages Required

5+ page

Font styles to use
Sans Serif
Script

Colors
fdf0f6

Requirements
Must have
• The logo provided
• Ability to change page contents easily
• Ability to add social media icons as needed
Nice to have
• Use of the typewriter image
Should not have
• Complicated pages that are not easily editable

```html
<!DOCTYPE html>
<html lang="en">
<head>
<meta charset="utf-8">
<title>Mara Penrith Copywriter</title>
<link href="https://fonts.googleapis.com/css2?family=Poppins:wght@400;500;600;700&family=Lobster&display=swap" rel="stylesheet">
<style>
:root{
  --ink:#111111;
  --dark:#1b1b1b;
  --white:#ffffff;
  --blush:#fdf0f6;
  --brush:#f6d9e3;
  --grey:#efefef;
  --text:#333333;
  --muted:#777777;
}
*{margin:0;padding:0;box-sizing:border-box}
html,body{width:1200px;height:4054px;overflow:hidden}
body{position:relative;background:var(--white);font-family:'Poppins',sans-serif;color:var(--text)}
.abs{position:absolute}
.site-header{position:absolute;left:0;top:0;width:1200px;height:108px;background:var(--white)}
.logo{position:absolute;left:135px;top:22px;width:300px;height:66px;background:var(--brush);border-radius:30px 6px 30px 6px;display:flex;align-items:center;justify-content:center;font-size:22px;font-weight:500;color:var(--ink)}
.contact-line{position:absolute;top:20px;font-size:17px;color:var(--ink);display:flex;align-items:center;gap:12px}
.contact-line .dot{width:24px;height:24px;border-radius:50%;background:var(--brush);display:flex;align-items:center;justify-content:center}
.main-nav{position:absolute;top:68px;left:0;width:1200px;font-size:15px;font-weight:600;color:var(--ink)}
.main-nav span{position:absolute}
.hero{position:absolute;left:0;top:108px;width:1200px;height:560px;background:linear-gradient(135deg,#4a4743,#2a2826 50%,#3e3a36)}
.hero-title{position:absolute;width:1200px;text-align:center;color:var(--white);font-family:'Lobster',cursive}
.btn-outline{position:absolute;border:2px solid var(--ink);border-radius:20px;font-size:13px;font-weight:600;text-align:center;line-height:30px;height:34px;color:var(--ink)}
.btn-light{border-color:var(--white);color:var(--white)}
.slide-arrow{position:absolute;top:282px;width:32px;height:32px;border-radius:50%;background:rgba(255,255,255,.15)}
.photo{position:absolute;box-shadow:0 4px 16px rgba(0,0,0,.25);border:8px solid var(--white)}
.brush-heading{position:absolute;background:var(--brush);border-radius:40px 8px 40px 8px;font-weight:700;font-size:40px;color:var(--ink);display:flex;align-items:center;justify-content:center;letter-spacing:1px}
.para{position:absolute;font-size:15px;line-height:29px;color:var(--text)}
.business{position:absolute;left:0;top:1270px;width:1200px;height:582px;background:var(--grey)}
.services-text{color:#e6e6e6}
.service-card{position:absolute;top:1995px;width:296px;height:243px;background:var(--blush);text-align:center;font-weight:700;font-size:19px;color:var(--ink)}
.service-card::after{content:"";position:absolute;left:134px;bottom:-14px;border-left:14px solid transparent;border-right:14px solid transparent;border-top:14px solid var(--blush)}
.service-photo{position:absolute;top:2257px;width:296px;height:251px}
.post-title{position:absolute;font-size:17px;font-weight:600;color:var(--ink)}
.post-date{position:absolute;font-size:12px;font-weight:600;color:var(--ink)}
.post-text{position:absolute;font-size:12.5px;line-height:23px;color:var(--text)}
.partners{position:absolute;left:0;top:3297px;width:1200px;height:230px;background:var(--grey)}
.partner{position:absolute;top:3371px;width:176px;height:78px;background:var(--white);display:flex;align-items:center;justify-content:center;font-size:24px;font-weight:600;color:#555}
.site-footer{position:absolute;left:0;top:3527px;width:1200px;height:527px;background:var(--ink);color:var(--white)}
.foot-head{position:absolute;font-size:20px;font-weight:700}
.foot-item{position:absolute;font-size:13px;line-height:23px}
</style>
</head>
<body>

<header class="site-header">
  <div class="logo">Mara Penrith Copywriter</div>
  <div class="contact-line" style="left:570px">
    <span class="dot"><svg width="12" height="12" viewBox="0 0 24 24"><path d="M6 2l4 5-2 3c1 3 3 5 6 6l3-2 5 4-3 4C10 22 2 14 2 5z" fill="#111"/></svg></span>0412 583 906</div>
  <div class="contact-line" style="left:755px">
    <span class="dot"><svg width="12" height="12" viewBox="0 0 24 24"><rect x="2" y="5" width="20" height="14" fill="none" stroke="#111" stroke-width="2"/><path d="M2 5l10 8 10-8" fill="none" stroke="#111" stroke-width="2"/></svg></span>mara.penrith.copywriter@fernmail.test</div>
  <nav class="main-nav">
    <span style="left:614px">HOME</span><span style="left:690px">SERVICES</span><span style="left:797px">PORTFOLIO</span><span style="left:919px">BLOG</span><span style="left:992px">CONTACT</span>
  </nav>
</header>

<section class="hero" role="img" aria-label="Desk with a vintage typewriter, coffee cups and papers">
  <div class="hero-title" style="top:140px;font-size:56px">Hi, I'm</div>
  <div class="hero-title" style="top:205px;font-size:76px">Mara Penrith</div>
  <div class="btn-outline btn-light" style="left:519px;top:340px;width:162px">GET MORE INFO</div>
  <div class="slide-arrow" style="left:98px"><svg width="32" height="32"><path d="M19 9l-7 7 7 7" stroke="#fff" stroke-width="3" fill="none"/></svg></div>
  <div class="slide-arrow" style="left:1068px"><svg width="32" height="32"><path d="M13 9l7 7-7 7" stroke="#fff" stroke-width="3" fill="none"/></svg></div>
</section>

<section class="about">
  <div class="photo" role="img" aria-label="Portrait of the copywriter writing at her desk" style="left:135px;top:803px;width:388px;height:359px;background:linear-gradient(135deg,#d9d4cf,#b9b2ab)"></div>
  <div class="brush-heading" style="left:562px;top:824px;width:398px;height:73px">ABOUT ME</div>
  <p class="para" style="left:570px;top:933px;width:500px">Sed ut perspiciatis unde omnis iste natus error sit voluptatem accusantium doloremque laudantium, totam rem aperiam, eaque ipsa quae ab illo inventore veritatis et quasi architecto beatae vitae dicta sunt explicabo. Nemo enim ipsam voluptatem quia voluptas sit aspernatur aut odit aut fugit, sed quia consequuntur</p>
  <div class="btn-outline" style="left:570px;top:1110px;width:120px">READ MORE</div>
</section>

<section class="business">
  <div class="brush-heading" style="left:122px;top:135px;width:392px;height:71px">MY BUSINESS</div>
  <p class="para" style="left:132px;top:243px;width:500px">Sed ut perspiciatis unde omnis iste natus error sit voluptatem accusantium doloremque laudantium, totam rem aperiam, eaque ipsa quae ab illo inventore veritatis et quasi architecto beatae vitae dicta sunt explicabo. Nemo enim ipsam voluptatem quia voluptas sit aspernatur aut odit aut fugit, sed quia consequuntur</p>
  <div class="btn-outline" style="left:132px;top:418px;width:120px">READ MORE</div>
  <div class="photo" role="img" aria-label="Black vintage typewriter with a blank sheet" style="left:676px;top:108px;width:392px;height:365px;background:linear-gradient(180deg,#f4f4f4,#cfcfcf 55%,#3a3a3a)"></div>
</section>

<svg class="abs" style="left:0;top:1852px" width="1200" height="689"><polygon points="0,0 1200,0 1200,419 0,689" fill="#1b1b1b"/></svg>
<section class="services">
  <div class="abs" style="left:98px;top:2015px;width:2px;height:82px;background:#fff"></div>
  <div class="abs" style="left:95px;top:2052px;width:8px;height:8px;border-radius:50%;background:#fff"></div>
  <div class="abs" style="left:126px;top:2020px;font-size:52px;font-weight:700;color:#333">MY SERVICES</div>
  <div class="abs" style="left:157px;top:2028px;font-size:50px;font-weight:600;color:#fff;letter-spacing:1px">SERVICES</div>
  <p class="para services-text" style="left:98px;top:2128px;width:360px;font-size:14px;line-height:28px">Lorem ipsum dolor sit amet, consectetur adipiscing elit, sed do eiusmod tempor incididunt ut labore et dolore magna aliqua. Ut enim ad minim veniam, quis nostrud exercitation ullamco laboris</p>
  <p class="para services-text" style="left:98px;top:2264px;width:360px;font-size:14px;line-height:28px">Sed ut perspiciatis unde omnis iste natus error sit voluptatem accusantium doloremque laudantium, totam rem aperiam, eaque ipsa quae</p>
  <div class="service-card" style="left:495px">
    <svg style="margin-top:72px" width="56" height="50" viewBox="0 0 56 50"><rect x="16" y="2" width="24" height="16" fill="none" stroke="#111" stroke-width="2.5"/><rect x="4" y="18" width="48" height="26" rx="3" fill="none" stroke="#111" stroke-width="2.5"/><path d="M12 28h32M12 35h32" stroke="#111" stroke-width="2.5"/></svg>
    <div style="margin-top:14px">TYPEWRITER</div></div>
  <div class="service-card" style="left:808px">
    <svg style="margin-top:72px" width="56" height="50" viewBox="0 0 56 50"><path d="M14 40L38 8l8 6-24 32-10 2z" fill="none" stroke="#111" stroke-width="2.5"/><path d="M8 48c10-4 20 2 30-2" fill="none" stroke="#111" stroke-width="2"/></svg>
    <div style="margin-top:14px">COPYWRITER</div></div>
  <div class="service-photo" role="img" aria-label="Hands typing on a vintage typewriter" style="left:495px;background:linear-gradient(135deg,#8a7b6c,#3b342d)"></div>
  <div class="service-photo" role="img" aria-label="Person typing on a laptop at a wooden desk" style="left:808px;background:linear-gradient(135deg,#ddd3c6,#9a8674)"></div>
</section>

<section class="blog">
  <div class="brush-heading" style="left:400px;top:2620px;width:405px;height:74px">LATEST BLOG</div>
  <div class="abs" style="left:599px;top:2730px;width:2px;height:68px;background:#111"></div>
  <div class="abs" style="left:595px;top:2758px;width:10px;height:10px;border-radius:50%;background:#111"></div>

  <div class="abs" role="img" aria-label="Colleagues reviewing a tablet together" style="left:132px;top:2835px;width:406px;height:214px;background:linear-gradient(135deg,#7c8a8c,#b89a46)"></div>
  <div class="post-title" style="left:132px;top:3064px">Nemo enim ipsam voluptatem quia voluptas</div>
  <div class="post-date" style="left:132px;top:3100px">&#9638; JULY 05, 2018</div>
  <p class="post-text" style="left:132px;top:3122px;width:406px">Lorem ipsum dolor sit amet, consectetur adipiscing elit, sed do eiusmod tempor incididunt ut labore et dolore magna aliqua. Ut enim ad minim veniam</p>

  <div class="abs" role="img" aria-label="Laptop on a cafe table" style="left:573px;top:2835px;width:203px;height:165px;background:linear-gradient(135deg,#a36a3c,#4d3a2d)"></div>
  <div class="post-title" style="left:797px;top:2837px">Nemo enim ipsam voluptatem</div>
  <div class="post-date" style="left:797px;top:2872px">&#9638; JULY 05, 2018</div>
  <p class="post-text" style="left:797px;top:2898px;width:280px">Lorem ipsum dolor sit amet, consectetur adipiscing elit, sed do eiusmod tempor didunt ut labore et dolore magna aliqua. Lorem ipsum dolor sit amet, consectetur adipiscing</p>

  <div class="abs" role="img" aria-label="Notebook and charts on an office desk" style="left:573px;top:3030px;width:203px;height:162px;background:linear-gradient(135deg,#b8c3cc,#5c6b78)"></div>
  <div class="post-title" style="left:797px;top:3030px">Nemo enim ipsam voluptatem</div>
  <div class="post-date" style="left:797px;top:3065px">&#9638; JULY 05, 2018</div>
  <p class="post-text" style="left:797px;top:3091px;width:280px">Lorem ipsum dolor sit amet, consectetur adipiscing elit, sed do eiusmod tempor didunt ut labore et dolore magna aliqua. Lorem ipsum dolor sit amet, consectetur adipiscing</p>
</section>

<section class="partners">
  <svg class="abs" style="left:88px;top:95px" width="24" height="40"><path d="M18 4L6 20l12 16" stroke="#bbb" stroke-width="3" fill="none"/></svg>
  <svg class="abs" style="left:1088px;top:95px" width="24" height="40"><path d="M6 4l12 16L6 36" stroke="#bbb" stroke-width="3" fill="none"/></svg>
</section>
<div class="partner" style="left:132px">Launchwise</div>
<div class="partner" style="left:322px">Brightfeed</div>
<div class="partner" style="left:511px">Orbitnow</div>
<div class="partner" style="left:700px">MKTV</div>
<div class="partner" style="left:892px">Techlane</div>

<footer class="site-footer">
  <div class="foot-head" style="left:132px;top:140px">CONTACT US</div>
  <svg class="abs" style="left:132px;top:206px" width="16" height="20" viewBox="0 0 16 20"><path d="M8 19C3 12 2 10 2 7a6 6 0 0112 0c0 3-1 5-6 12z" fill="none" stroke="#fff" stroke-width="1.6"/><circle cx="8" cy="7" r="2" fill="#fff"/></svg>
  <div class="foot-item" style="left:166px;top:200px">Mara Penrith<br>Birchmount Lane Realty,<br>Brokerage</div>
  <svg class="abs" style="left:132px;top:274px" width="16" height="16" viewBox="0 0 24 24"><path d="M6 2l4 5-2 3c1 3 3 5 6 6l3-2 5 4-3 4C10 22 2 14 2 5z" fill="#fff"/></svg>
  <div class="foot-item" style="left:166px;top:270px">Phone: 0412 583 906</div>
  <svg class="abs" style="left:132px;top:308px" width="16" height="16" viewBox="0 0 16 16"><rect x="1" y="6" width="14" height="9" fill="#fff"/><rect x="4" y="1" width="8" height="5" fill="none" stroke="#fff" stroke-width="1.5"/></svg>
  <div class="foot-item" style="left:166px;top:304px">Fax: 0412 583 906</div>
  <svg class="abs" style="left:132px;top:342px" width="16" height="14" viewBox="0 0 24 20"><rect x="1" y="2" width="22" height="16" fill="none" stroke="#fff" stroke-width="2"/><path d="M1 2l11 9 11-9" fill="none" stroke="#fff" stroke-width="2"/></svg>
  <div class="foot-item" style="left:166px;top:338px">mara.penrith.copywriter@fernmail.test</div>

  <div class="foot-head" style="left:500px;top:140px">QUICK LINKS</div>
  <div class="foot-item" style="left:500px;top:196px;line-height:24.5px">&#9679;&nbsp;&nbsp; Home<br>&#9679;&nbsp;&nbsp; About Us<br>&#9679;&nbsp;&nbsp; Services<br>&#9679;&nbsp;&nbsp; Portfolio<br>&#9679;&nbsp;&nbsp; Blog<br>&#9679;&nbsp;&nbsp; Contact</div>

  <div class="foot-head" style="left:722px;top:140px">SIGN UP FOR NEWSLETTER</div>
  <div class="foot-item" style="left:722px;top:196px">Nemo enim ipsam voluptatem quia voluptas sit aspernatur</div>
  <div class="abs" style="left:722px;top:235px;width:346px;height:38px;background:#fff;display:flex;align-items:center">
    <span style="font-size:12px;color:#888;padding-left:14px;flex:1">Enter email</span>
    <span style="height:38px;width:112px;background:var(--blush);color:#111;font-size:12px;font-weight:700;line-height:38px;text-align:center">SUBSCRIPTION</span>
  </div>
  <div class="abs" style="left:722px;top:306px;display:flex;gap:8px">
    <span style="width:28px;height:28px;border:1.5px solid #fff;border-radius:50%"></span>
    <span style="width:28px;height:28px;border:1.5px solid #fff;border-radius:50%"></span>
    <span style="width:28px;height:28px;border:1.5px solid #fff;border-radius:50%"></span>
    <span style="width:28px;height:28px;border:1.5px solid #fff;border-radius:50%"></span>
  </div>

  <div class="abs" style="left:0;top:414px;width:1200px;height:1px;background:#333"></div>
  <div class="abs" style="left:0;top:455px;width:1200px;text-align:center;font-size:13px">(c) 2018 Mara Penrith | All Rights Reserved | Disclaimer</div>
</footer>

</body>
</html>
```